BrindleStaffing Business Card Design

We are a staffing company finding positions for dedicated nurses and physicians.

Target Market(s)

Business Professionals

Industry/Entity Type

Staffing

Contact Information for Business Card

Gordon Pratley
Chairman
417 39th Avenue South
SAINT PETERSBURG FL 33712
813-555-4172 Mobile
813-555-8036 Fax
gpratley@brindlestaffing.com
www.brindlestaffing.com

Font styles to use
Sans Serif

Colors
fbee3e
f04a50
f37122

Requirements
Must have
• Logo Attached, see colors below. We'd like to see Yellow, Orange and Red.

```html
<!DOCTYPE html>
<html lang="en">
<head>
<meta charset="utf-8">
<title>BrindleStaffing Business Card</title>
<link rel="stylesheet" href="https://fonts.googleapis.com/css2?family=Roboto:wght@400;500;700&display=swap">
<style>
  :root {
    --backdrop: #2a2a2a;
    --card-white: #ffffff;
    --brand-yellow: #fbee3e;
    --brand-red: #f04a50;
    --brand-orange: #f37122;
    --text-grey: #8a8a8a;
    --text-dark: #4a4a4a;
    --rule-grey: #8f8f8f;
  }
  * { margin: 0; padding: 0; box-sizing: border-box; }
  html, body {
    width: 1125px; height: 1200px; overflow: hidden;
    background: var(--backdrop);
    font-family: "Roboto", Arial, sans-serif;
  }
  .card {
    position: absolute; left: 150px; width: 825px; height: 471px;
    overflow: hidden;
  }
  .card-front { top: 98px; background: var(--card-white); }
  .card-back { top: 631px; background: var(--brand-orange); }

  .brand-name {
    position: absolute; right: 43px; top: 60px;
    font-size: 44px; font-weight: 700; letter-spacing: -0.5px;
    color: var(--brand-orange);
  }

  .holder-name {
    position: absolute; left: 40px; top: 252px;
    font-size: 28px; font-weight: 700; color: var(--brand-red);
  }
  .holder-title {
    position: absolute; left: 40px; top: 284px;
    font-size: 20px; font-weight: 400; color: var(--brand-orange);
  }
  .divider {
    position: absolute; left: 49px; top: 326px; width: 732px; height: 2px;
    background: var(--rule-grey);
  }
  .contact-list {
    position: absolute; left: 47px; top: 348px; list-style: none;
  }
  .contact-list li {
    display: flex; align-items: center; height: 26px;
    font-size: 19px; color: var(--text-grey);
  }
  .contact-list svg { width: 18px; height: 18px; margin-right: 10px; fill: var(--brand-orange); }
  .address {
    position: absolute; right: 43px; top: 349px; text-align: right;
    font-size: 19px; line-height: 25px; color: var(--text-dark);
    font-style: normal;
  }
  .edge-line {
    position: absolute; left: 0; bottom: 17px; width: 100%; height: 3px;
    background: var(--brand-yellow);
  }
  .edge-band {
    position: absolute; left: 0; bottom: 0; width: 100%; height: 15px;
    background: var(--brand-red);
  }

  .back-brand {
    position: absolute; right: 47px; top: 360px;
    font-size: 38px; font-weight: 700; letter-spacing: -0.5px;
    color: var(--card-white);
  }
  .back-url {
    position: absolute; right: 47px; top: 405px;
    font-size: 18px; letter-spacing: 2px; color: var(--card-white);
  }
</style>
</head>
<body>
  <section class="card card-front">
    <div class="brand-name">BrindleStaffing</div>

    <div class="holder-name">Gordon Pratley</div>
    <div class="holder-title">Chairman</div>
    <div class="divider"></div>

    <ul class="contact-list">
      <li>
        <svg viewBox="0 0 18 18" aria-hidden="true"><path d="M5 1h8a1.5 1.5 0 0 1 1.5 1.5v13A1.5 1.5 0 0 1 13 17H5a1.5 1.5 0 0 1-1.5-1.5v-13A1.5 1.5 0 0 1 5 1zm0.5 2v10h7V3zm3.5 11.2a1 1 0 1 0 0 2 1 1 0 0 0 0-2z"/></svg>
        813-555-4172
      </li>
      <li>
        <svg viewBox="0 0 18 18" aria-hidden="true"><path d="M5 2h8v4H5zM2 7h14a1 1 0 0 1 1 1v6H1V8a1 1 0 0 1 1-1zm2 8h10v2H4z"/></svg>
        813-555-8036
      </li>
      <li>
        <svg viewBox="0 0 18 18" aria-hidden="true"><path d="M1 4h16v10H1zm1.5 1.2L9 10l6.5-4.8V5H2.5z"/></svg>
        gpratley@brindlestaffing.com
      </li>
    </ul>

    <address class="address">
      417 39th Avenue South<br>
      SAINT PETERSBURG FL 33712<br>
      www.brindlestaffing.com
    </address>

    <div class="edge-line"></div>
    <div class="edge-band"></div>
  </section>

  <section class="card card-back">
    <div class="back-brand">BrindleStaffing</div>
    <div class="back-url">www.brindlestaffing.com</div>
  </section>
</body>
</html>
```